Social Media App Needs PPT Template

We need a PowerPoint template for a new social media company based in the DC area called "Bold Ledger." We provide an interactive digital platform for executives to share actionable advice. We would like to see designs that use our orange logo color as an accent, but are mainly grey, white, and black. The final design should communicate clean, chic, modern, and professional.

Target Market(s)

Executives

Industry/Entity Type

Information Technology

Font styles to use
Sans Serif

Colors
f78f20
fbe7d2
ffffff
000000
e8e8e8
757575

Requirements
Must have
• My project must have title page and many options for the body of the ppt (graphs, tables, etc). It also needs to be easy to modify. I must have someone who is experienced in creating powerpoint templates.
Nice to have
• It would be nice to have a very modern and clean design that includes the logo on every page, but still leaves a lot of room for the content of the slide
Should not have
• My design project should not look to busy.

```html
<!DOCTYPE html>
<html lang="en">
<head>
<meta charset="utf-8">
<title>Why social media works</title>
<link href="https://fonts.googleapis.com/css2?family=Source+Sans+3:wght@400;700&family=Arimo:wght@700&display=swap" rel="stylesheet">
<style>
  :root {
    --ink: #000000;
    --paper: #ffffff;
    --orange: #f78f20;
    --cream: #fbe7d2;
    --mist: #e8e8e8;
    --slate: #757575;
    --silver: #c4c4c4;
  }
  html, body { margin: 0; padding: 0; overflow: hidden; background: var(--paper); }
  .slide {
    position: relative;
    width: 1200px;
    height: 900px;
    overflow: hidden;
    background: var(--paper);
    font-family: "Source Sans 3", "Myriad Pro", sans-serif;
    color: var(--ink);
  }
  .slide-frame { position: absolute; inset: 0; width: 1200px; height: 900px; }
  .slide-title {
    position: absolute;
    left: 70px;
    top: 38px;
    margin: 0;
    font-family: "Arimo", Arial, sans-serif;
    font-weight: 700;
    font-size: 64px;
    line-height: 80px;
    letter-spacing: 0.5px;
    color: var(--ink);
    white-space: nowrap;
  }
  .point {
    position: absolute;
    margin: 0;
    font-size: 36px;
    line-height: 46px;
    white-space: nowrap;
  }
  .point-social { left: 378px; top: 209px; }
  .point-sharing { left: 253px; top: 499px; font-size: 37px; }
  .point-friends {
    left: 62px; top: 640px; width: 500px;
    font-size: 38px;
    text-align: center;
    white-space: normal;
  }
  .conclusion {
    position: absolute;
    left: 58px;
    top: 784px;
    margin: 0;
    font-size: 43px;
    line-height: 56px;
    font-weight: 700;
    white-space: nowrap;
  }
  .visual { position: absolute; }
  .visual-circle-people {
    left: 76px; top: 164px; width: 232px; height: 204px;
    border-radius: 50%;
    background: radial-gradient(circle at 50% 50%, var(--paper) 0%, var(--paper) 34%, var(--cream) 36%, #f5c89a 62%, var(--mist) 100%);
  }
  .visual-conversation {
    left: 428px; top: 288px; width: 328px; height: 198px;
    background: linear-gradient(180deg, var(--cream) 0%, #f3c79c 55%, var(--silver) 100%);
  }
  .visual-network {
    left: 584px; top: 564px; width: 348px; height: 192px;
    background: linear-gradient(180deg, var(--mist) 0%, #cfd3dc 60%, var(--silver) 100%);
  }
  .brand-badge {
    position: absolute;
    left: 1005px; top: 715px;
    width: 166px; height: 166px;
    border-radius: 50%;
    background: var(--paper);
    display: flex; align-items: center; justify-content: center;
  }
  .brand-name {
    font-size: 24px;
    font-weight: 700;
    color: var(--ink);
    white-space: nowrap;
  }
</style>
</head>
<body>
<div class="slide">
  <svg class="slide-frame" viewBox="0 0 1200 900" aria-hidden="true">
    <polygon points="920,0 1200,0 1200,900 1120,900 1092,640" fill="var(--orange)"/>
    <polygon points="1060,0 1176,0 1126,560" fill="var(--slate)"/>
    <polygon points="1176,0 1200,0 1200,720 1126,560" fill="var(--silver)"/>
    <polygon points="1092,640 1126,560 1160,900 1010,900" fill="var(--cream)"/>
    <polygon points="1126,560 1200,720 1200,900 1160,900" fill="var(--mist)"/>
    <polygon points="872,900 1200,715 1200,900" fill="var(--orange)"/>
    <polygon points="0,536 0,900 58,900" fill="var(--orange)"/>
  </svg>

  <h1 class="slide-title">Why social media Works ?</h1>

  <div class="visual visual-circle-people" role="img" aria-label="Illustration of colourful paper figures holding hands in a circle"></div>
  <p class="point point-social">Human being is Social</p>

  <div class="visual visual-conversation" role="img" aria-label="Illustration of colourful figures with speech bubbles above them"></div>
  <p class="point point-sharing">We love telling others, sharing Contents, Ideas</p>

  <p class="point point-friends">And Will want to share it with other Friend</p>
  <div class="visual visual-network" role="img" aria-label="Illustration of colourful figures connected around a globe"></div>

  <p class="conclusion">Multipal Interaction are just a matter of time</p>

  <div class="brand-badge"><span class="brand-name">Bold Ledger</span></div>
</div>
</body>
</html>
```